My Business is Car Dealership, we sale cars and trucks, I’m looking for a sign design
I need 2 signage
9ā€ by 7ā€ feet.
the other sign is 3" feet high and the width is 12" feet

For further reference about the company , you can check my website
www.harrowvaleautosale.com

Industry/Entity Type

Business

Requirements
Must have
• picture of 2018 brask T390 or 2018 Dunmoreau Tallwind
Nice to have
• the business name Harrow Vale Auto Sale visible from far distance

```html
<!DOCTYPE html>
<html lang="en">
<head>
<meta charset="utf-8">
<title>Harrow Vale Auto Sale – Sign 9x7 ft</title>
<link rel="stylesheet" href="https://fonts.googleapis.com/css2?family=Montserrat:wght@600;700;800&display=swap">
<style>
  :root {
    --page: #ffffff;
    --sign-black: #0b0b0b;
    --brand-red: #e3121b;
    --glow-red: #8c0d12;
    --white: #ffffff;
    --tagline-grey: #9a9a9a;
    --silver-light: #e6e7e9;
    --silver-mid: #b9bcc0;
    --label-ink: #111111;
  }
  * { margin: 0; padding: 0; box-sizing: border-box; }
  html, body {
    width: 1200px; height: 1200px; overflow: hidden;
    background: var(--page);
  }
  .sign {
    position: absolute;
    left: 100px; top: 211px;
    width: 1000px; height: 778px;
    background: var(--sign-black);
    overflow: hidden;
  }
  .brand {
    position: absolute; left: 0; right: 0; top: 26px;
    text-align: center;
    font-family: "Montserrat", sans-serif;
    font-weight: 800;
    color: var(--brand-red);
    line-height: 1;
  }
  .brand-line { display: block; }
  .brand-line-top { font-size: 96px; letter-spacing: 1px; }
  .brand-line-bottom { font-size: 84px; margin-top: 6px; }
  .vehicle-photo {
    position: absolute;
    left: 140px; top: 228px;
    width: 730px; height: 320px;
    background: radial-gradient(ellipse 48% 50% at 52% 52%,
      var(--silver-light) 0%, var(--silver-mid) 38%, var(--glow-red) 62%, rgba(140,13,18,0.35) 80%, transparent 100%);
  }
  .tagline {
    position: absolute;
    left: 0; right: 0; top: 552px;
    text-align: center;
    font-family: "Montserrat", sans-serif;
    font-weight: 700;
    font-size: 32px;
    letter-spacing: 6px;
    color: var(--tagline-grey);
    white-space: nowrap;
  }
  .phone {
    position: absolute;
    left: 0; right: 0; top: 600px;
    text-align: center;
    font-family: "Montserrat", sans-serif;
    font-weight: 800;
    font-size: 90px;
    letter-spacing: 3px;
    color: var(--white);
    line-height: 1;
  }
  .website {
    position: absolute;
    left: 0; right: 0; top: 712px;
    text-align: center;
    font-family: "Montserrat", sans-serif;
    font-weight: 700;
    font-size: 22px;
    letter-spacing: 13px;
    color: var(--white);
    white-space: nowrap;
  }
  .size-note {
    position: absolute;
    left: 1112px; top: 960px;
    font-family: "Montserrat", sans-serif;
    font-weight: 600;
    font-size: 20px;
    color: var(--label-ink);
  }
</style>
</head>
<body>
  <div class="sign">
    <h1 class="brand">
      <span class="brand-line brand-line-top">Harrow Vale</span>
      <span class="brand-line brand-line-bottom">Auto Sale</span>
    </h1>

    <div class="vehicle-photo" role="img" aria-label="Photo of a silver 2018 brask T390 pickup truck on a red glow"></div>

    <p class="tagline">Quality Pre-Owned Vehicles</p>
    <p class="phone">831-555-0142</p>
    <p class="website">www.harrowvaleautosale.com</p>
  </div>
  <p class="size-note">9x7ft</p>
</body>
</html>
```